Velmora Nightclub Flyer (Updated)

Flyer for facebook, square is fine, or rectangular. Here is the text:
VELMORA
Nightclub + Lounge
presents

B2B THURSDAY
Nov 29 2018

CLUB FLOOR:
ROLF B2B GARTH
BENEDICT SALVORTE

LOUNGE:
TOBY B2B MY COUSIN
THUNDER REGGIE

Powered by KELP Acoustics
4726 8th Avenue 21+ 9pm-2am
velmorakestrel.com for VIP booth inquiries

Target Market(s)

Nightclub

Industry/Entity Type

Night Club

Font styles to use
Sans Serif

Colors

Designer to choose colors to be used in the design.

Requirements
Must have
• All the text listed, and plz keep the theme of the attached files. We want to stay consistent with the Velmora brand
Nice to have
• Try to stay with the theme from the attachments
Should not have
• Dont' stray to far from the general theme we have from the attachments

```html
<!DOCTYPE html>
<html lang="en">
<head>
<meta charset="utf-8">
<title>Velmora – B2B Thursday Flyer</title>
<link href="https://fonts.googleapis.com/css2?family=Bodoni+Moda:wght@400;500&family=Libre+Bodoni:wght@700&family=Montserrat:wght@400;500&family=Oswald:wght@600&display=swap" rel="stylesheet">
<style>
  :root {
    --page: #ffffff;
    --ink: #231f20;
    --white: #ffffff;
    --gold: #c9a063;
    --gold-deep: #9c7435;
    --label-grey: #6d6b6c;
    --rule: #6b5a3e;
  }
  * { margin: 0; padding: 0; box-sizing: border-box; }
  html, body {
    width: 1200px; height: 1200px; overflow: hidden;
    background: var(--page);
  }
  .flyer {
    position: absolute; left: 170px; top: 376px;
    width: 862px; height: 451px;
    background: var(--ink); overflow: hidden;
    color: var(--white);
  }
  .ornament {
    position: absolute; left: 0; top: 137px;
    width: 320px; height: 314px;
  }
  .brand {
    position: absolute; left: 0; right: 0; top: 38px;
    text-align: center;
    font-family: "Bodoni Moda", serif; font-weight: 400;
    font-size: 80px; line-height: 1; letter-spacing: 1px;
  }
  .tagline {
    position: absolute; left: 0; right: 0; top: 124px;
    text-align: center;
    font-family: "Montserrat", sans-serif; font-weight: 400;
    font-size: 15px; line-height: 18px; letter-spacing: 4px;
  }
  .date-box {
    position: absolute; left: 422px; top: 196px;
    width: 155px; height: 41px;
    border: 1px solid var(--rule);
    display: flex; align-items: center; justify-content: center;
    font-family: "Bodoni Moda", serif; font-weight: 500;
    font-size: 22px; color: var(--gold); letter-spacing: 0.5px;
  }
  .event-title {
    position: absolute; left: 589px; top: 198px;
    font-family: "Libre Bodoni", serif; font-weight: 700;
    font-size: 22px; letter-spacing: 0.5px;
  }
  .title-rule {
    position: absolute; left: 589px; top: 236px;
    width: 212px; height: 8px;
  }
  .lineup {
    position: absolute; left: 420px; width: 400px;
    display: grid; grid-template-columns: 156px 1fr; column-gap: 13px;
  }
  .lineup.club { top: 418px; }
  .lineup.lounge { top: 480px; }
  .lineup { top: auto; }
  .stage-label {
    text-align: right;
    font-family: "Oswald", sans-serif; font-weight: 600;
    font-size: 13px; letter-spacing: 1.5px; color: var(--label-grey);
    line-height: 22px;
  }
  .stage-acts {
    font-family: "Montserrat", sans-serif; font-weight: 400;
    font-size: 15px; line-height: 22px;
  }
  .footer {
    position: absolute; left: 420px; top: 384px;
    width: 380px; padding: 8px 7px 0;
    border-top: 1px solid var(--rule);
    font-family: "Montserrat", sans-serif; font-weight: 400;
    font-size: 9.6px; line-height: 15px; letter-spacing: 1px;
    color: var(--gold);
  }
  .footer-end {
    position: absolute; left: 418px; top: 432px;
    width: 380px; border-top: 1px solid var(--rule);
  }
  sup { font-size: 6px; vertical-align: 4px; }
</style>
</head>
<body>
  <main class="flyer">
    <svg class="ornament" viewBox="0 0 320 314" role="img" aria-label="Gold mandala ornament rising from the lower left corner">
      <defs>
        <radialGradient id="mandalaGold" cx="0" cy="314" r="314" gradientUnits="userSpaceOnUse">
          <stop offset="0" stop-color="#b88a4c"/>
          <stop offset="0.6" stop-color="#d4ab6c"/>
          <stop offset="1" stop-color="#c39457"/>
        </radialGradient>
      </defs>
      <circle cx="0" cy="314" r="314" fill="url(#mandalaGold)"/>
    </svg>

    <h1 class="brand">VELMORA</h1>
    <p class="tagline">NIGHTCLUB + LOUNGE<br>PRESENTS</p>

    <div class="date-box">NOV. 29. 2018</div>
    <h2 class="event-title">B2B Thursday</h2>
    <svg class="title-rule" viewBox="0 0 212 8">
      <line x1="0" y1="4" x2="196" y2="4" stroke="#8a7551" stroke-width="1"/>
      <circle cx="202" cy="4" r="3" fill="none" stroke="#8a7551" stroke-width="1"/>
      <circle cx="208" cy="4" r="2" fill="none" stroke="#8a7551" stroke-width="1"/>
    </svg>

    <section class="lineup" style="top:258px">
      <div class="stage-label">CLUB FLOOR:</div>
      <div class="stage-acts">ROLF B2B GARTH<br>BENEDICT SALVORTE</div>
    </section>
    <section class="lineup" style="top:320px">
      <div class="stage-label">LOUNGE:</div>
      <div class="stage-acts">TOBY B2B MY COUSIN<br>THUNDER REGGIE</div>
    </section>

    <footer class="footer">
      POWERED BY: KELP ACOUSTICS 4726 8<sup>TH</sup> AVENUE 21+ 9PM-2AM<br>
      VELMORAKESTREL.COM FOR VIP BOOTH INQUIRIES
    </footer>
    <div class="footer-end"></div>
  </main>
</body>
</html>
```